Advertising Material for Event

We are needing some advertising material done for an event. It can all be roughly the same except the two social media posts. We need:
- A banner
- A flyer
- 2 X social media posts

I have attached some examples of what we have done in the past. I have also attached a word document with the information.

Our colours are:
NAVY BLUE: Hex = #041E42 // RGB = 4 / 30 / 66 // CMYK = 100 / 90 / 13 / 68 // Pantone = 289 C
LIME GREEN: Hex = #97D700 // RGB = 151 / 215 / 0 // CMYK = 46 / 0 / 90 / 0 // Pantone = 375 C
WHITE

Our font are:
Avenir next regular, bold and demi bold
Freshman

Colors

Designer to choose colors to be used in the design.

Requirements
Must have
• Include photos provided. All info provided
Nice to have
• not cluttered

```html
<!DOCTYPE html>
<html lang="en">
<head>
<meta charset="utf-8">
<title>2022 Cheerleading Team Placements</title>
<link href="https://fonts.googleapis.com/css2?family=Graduate&family=Nunito+Sans:wght@400;700;800;900&family=Oswald:wght@500&display=swap" rel="stylesheet">
<style>
  :root {
    --navy: #041E42;
    --navy-deep: #0a1a3a;
    --lime: #97D700;
    --green: #4fae12;
    --green-dark: #1f6a2a;
    --white: #ffffff;
    --black: #03060c;
    --silver: #b9b9b9;
  }
  * { margin: 0; padding: 0; box-sizing: border-box; }
  html, body { width: 1200px; height: 1200px; overflow: hidden; background: var(--white); }
  body { font-family: "Nunito Sans", sans-serif; color: var(--white); position: relative; }

  .banner {
    position: absolute; left: 40px; top: 318px; width: 1120px; height: 564px; overflow: hidden;
    background: linear-gradient(180deg, #56b414 0%, #3f9a18 22%, #1d6b2c 40%, #0b3a3e 55%, var(--navy) 72%, var(--navy) 100%);
  }
  .abs { position: absolute; }

  .photo { position: absolute; }
  .photo-jump { left: 56px; top: 10px; width: 322px; height: 104px; border-radius: 50px;
    background: radial-gradient(ellipse at center, rgba(20,30,70,.85) 0%, rgba(20,30,70,.35) 60%, rgba(20,30,70,0) 75%); }
  .photo-stunt-left { left: 0; top: 100px; width: 160px; height: 444px;
    background: linear-gradient(180deg, rgba(230,190,160,.0) 0%, rgba(210,170,140,.55) 20%, rgba(30,40,70,.6) 60%, rgba(230,190,160,.55) 100%);
    border-radius: 40px 80px 10px 10px; }
  .photo-stunt-right { left: 916px; top: 0; width: 204px; height: 492px;
    background: linear-gradient(180deg, rgba(30,40,70,.0) 0%, rgba(180,210,90,.45) 18%, rgba(30,40,70,.6) 50%, rgba(230,200,180,.55) 85%, rgba(230,200,180,.0) 100%);
    border-radius: 80px 0 30px 60px; }

  .year-title {
    left: 0; width: 1120px; top: 14px; text-align: center;
    font-family: "Graduate", serif; font-size: 98px; line-height: 1; letter-spacing: -4px;
    color: var(--green); -webkit-text-stroke: 3px var(--navy);
    background: linear-gradient(180deg, #0b1f33 0%, #2a7a2a 45%, #6fd21a 100%);
    -webkit-background-clip: text; background-clip: text; -webkit-text-fill-color: transparent;
  }
  .main-title {
    left: 0; width: 1120px; top: 110px; text-align: center;
    font-family: "Graduate", serif; font-size: 60px; line-height: 1; letter-spacing: -1px;
    background: linear-gradient(90deg, #f4f4f4 0%, #e2e2e2 45%, #9a9a9a 100%);
    -webkit-background-clip: text; background-clip: text; -webkit-text-fill-color: transparent;
  }
  .sub-title {
    left: 0; width: 1120px; top: 172px; text-align: center;
    font-weight: 900; font-size: 29px; line-height: 1; letter-spacing: .5px;
  }

  .intro-band {
    left: 219px; top: 214px; width: 683px; height: 58px;
    background: linear-gradient(90deg, var(--black) 0%, #10285a 50%, var(--black) 100%);
    clip-path: polygon(4% 0, 100% 0, 96% 100%, 0 100%);
    border-bottom: 2px solid var(--lime);
    display: flex; flex-direction: column; justify-content: center; align-items: center;
    font-weight: 800; font-size: 15.5px; line-height: 1.25; text-align: center;
  }
  .band-edge-left, .band-edge-right { width: 6px; height: 58px; background: var(--lime); }
  .band-edge-left { left: 219px; top: 214px; transform: skewX(-22deg); transform-origin: bottom; }
  .band-edge-right { left: 896px; top: 214px; transform: skewX(-22deg); transform-origin: top; }

  .date-card { left: 259px; top: 290px; width: 89px; height: 57px; background: var(--white);
    border-left: 3px solid var(--lime); color: var(--black); text-align: center; }
  .date-day { font-weight: 700; font-size: 10.5px; margin-top: 3px; }
  .date-num { font-weight: 900; font-size: 26px; line-height: 1; }
  .date-num sup { font-size: 14px; vertical-align: 9px; }
  .date-month { font-weight: 700; font-size: 9.5px; }
  .date-year { left: 348px; top: 290px; width: 82px; height: 57px; background: var(--navy-deep);
    font-family: "Oswald", sans-serif; font-weight: 500; font-size: 40px; line-height: 57px;
    color: var(--lime); text-align: center; }

  .session { top: 292px; width: 200px; text-align: center; }
  .session-one { left: 444px; }
  .session-two { left: 660px; }
  .session-label { font-weight: 800; font-size: 15px; color: var(--lime); }
  .session-label span { color: var(--white); }
  .session-time { font-weight: 900; font-size: 26px; line-height: 1.2; margin-top: 2px; }
  .session-divider { left: 652px; top: 294px; width: 1px; height: 48px; background: var(--green); }

  .detail-band {
    left: 231px; top: 362px; width: 653px; height: 37px; background: var(--black);
    clip-path: polygon(3% 0, 100% 0, 97% 100%, 0 100%);
    display: flex; align-items: center; justify-content: center; gap: 8px;
    font-weight: 700; font-size: 10.5px; white-space: nowrap;
  }
  .detail-band .cost { font-weight: 800; font-size: 13px; margin-left: 6px; }
  .detail-band .price { font-weight: 900; font-size: 29px; color: var(--lime); line-height: 1; }
  .detail-band .pack { font-size: 10px; margin-left: 4px; }
  .icon-pin { width: 12px; height: 14px; }

  .info-box { left: 182px; top: 426px; width: 732px; height: 66px;
    border: 1px solid rgba(255,255,255,.35); text-align: center; padding-top: 15px; }
  .info-box::before { content: ""; position: absolute; left: 199px; top: -2px; width: 333px; height: 4px; background: var(--navy); }
  .info-question { font-weight: 800; font-size: 12px; color: var(--lime); }
  .info-text { font-weight: 700; font-size: 9.6px; line-height: 1.3; padding: 0 18px; }
  .info-text em { font-style: normal; color: var(--lime); }
  .tag { left: 430px; top: 416px; width: 260px; height: 21px; background: var(--lime);
    clip-path: polygon(3% 0, 97% 0, 100% 100%, 0 100%);
    color: var(--navy); font-weight: 800; font-size: 10.5px; line-height: 21px; text-align: center; }

  .footer { left: 176px; top: 503px; width: 780px; height: 61px; background: var(--black);
    clip-path: polygon(4% 0, 92% 0, 100% 100%, 0 100%);
    display: flex; align-items: center; gap: 10px; padding-left: 54px;
    font-weight: 800; font-size: 15.5px; white-space: nowrap; }
  .brand { font-weight: 900; font-size: 22px; color: var(--white); margin-right: 8px; }
  .footer .phone { font-size: 19px; margin-right: 8px; }
  .footer .mail { margin-right: 6px; }
  .footer svg { width: 16px; height: 16px; flex: none; }
</style>
</head>
<body>
  <section class="banner">
    <div class="photo photo-jump" role="img" aria-label="Photo of a cheerleader in a toe-touch jump"></div>
    <div class="photo photo-stunt-left" role="img" aria-label="Photo of a cheer team holding a flyer in a stunt"></div>
    <div class="photo photo-stunt-right" role="img" aria-label="Photo of young cheerleaders lifting a flyer in a stunt"></div>

    <h1 class="abs year-title">2022</h1>
    <h2 class="abs main-title">CHEERLEADING</h2>
    <h3 class="abs sub-title">TEAM PLACEMENTS</h3>

    <div class="abs intro-band">
      <p>Try out for a cheerleading team!</p>
      <p>Everyone is welcome and will be placed on a team, regardless of skill level.</p>
    </div>
    <div class="abs band-edge-left"></div>
    <div class="abs band-edge-right"></div>

    <div class="abs date-card">
      <p class="date-day">SATURDAY</p>
      <p class="date-num">11<sup>th</sup></p>
      <p class="date-month">DECEMBER</p>
    </div>
    <div class="abs date-year">2021</div>

    <div class="abs session session-one">
      <p class="session-label">11 YEARS <span>AND</span> UNDER</p>
      <p class="session-time">3:30 - 4:30pm</p>
    </div>
    <div class="abs session-divider"></div>
    <div class="abs session session-two">
      <p class="session-label">12 YEARS <span>AND</span> OVER</p>
      <p class="session-time">4:45 - 5:45pm</p>
    </div>

    <div class="abs detail-band">
      <svg class="icon-pin" viewBox="0 0 12 14"><path d="M6 0C3 0 1 2.2 1 5c0 3.5 5 8 5 8s5-4.5 5-8c0-2.8-2-5-5-5z" fill="var(--lime)"/><circle cx="6" cy="5" r="1.8" fill="var(--black)"/></svg>
      <span>Nova Gymsports, 27 Harlow Street Westbrook</span>
      <span class="cost">COST:</span>
      <span class="price">$10</span>
      <span class="pack">and includes a Nova merchandise pack</span>
    </div>

    <div class="abs info-box">
      <p class="info-question">Unsure what cheerleading is like?</p>
      <p class="info-text">Come along to our open week to try it out with our current Nova cheerleading teams. Classes are available from the <em>6th-10th of December.</em> Please contact us for more information! Bookings are required.</p>
    </div>
    <div class="abs tag">SEMI-COMPETITIVE TEAMS ALSO AVAILABLE</div>

    <footer class="abs footer">
      <span class="brand">Nova</span>
      <svg viewBox="0 0 16 16"><path d="M3 1l3 3-1.5 2c1 2 3 4 5 5L11.5 9.5l3 3-2 2.5C7 14 2 9 1 3.5z" fill="var(--lime)"/></svg>
      <span class="phone">95550182</span>
      <svg viewBox="0 0 16 16"><rect x="1" y="3" width="14" height="10" fill="var(--lime)"/><path d="M1 3l7 6 7-6" stroke="var(--black)" stroke-width="1.3" fill="none"/></svg>
      <span class="mail">cheer@novagymsports.com</span>
      <svg viewBox="0 0 16 16"><circle cx="8" cy="8" r="7" fill="none" stroke="var(--lime)" stroke-width="1.5"/><ellipse cx="8" cy="8" rx="3" ry="7" fill="none" stroke="var(--lime)" stroke-width="1.2"/><path d="M1 8h14" stroke="var(--lime)" stroke-width="1.2"/></svg>
      <span>www.novagymsports.com</span>
    </footer>
  </section>
</body>
</html>
```